Road Construction Company needs business cards

We would like a new business card designed for our business.

We're a road construction company based in Qld, Australia.

Can the business card please have the following information on it.

Name: Warren Halbeck
Position: General Manager
Phone: 0472 915 348
Email: Warren.halbeck@tovrin.com.au
Address: 87 Marrow Ave, Pendlebay, QLD, 4023
Website: www.tovrin.com.au

Visually we'd like the card to be professional and simple.

Attached is our logo.

Our website is www.tovrin.com.au

Target Market(s)

Men aged 25-60

Contact Information for Business Card

As listed in project description

Font styles to use
Serif

Requirements
Must have
• Large logo on back of card

```html
<!DOCTYPE html>
<html lang="en">
<head>
<meta charset="utf-8">
<title>Tovrin Road Construction – Business Card</title>
<link href="https://fonts.googleapis.com/css2?family=Poppins:wght@300;400;600;800&display=swap" rel="stylesheet">
<style>
  :root {
    --backdrop: #969696;
    --card-dark: #231f20;
    --card-dark-mark: #151314;
    --card-light: #fbfbfb;
    --brand-navy: #0d4fa0;
    --brand-sky: #3aa5d8;
    --body-grey: #6b6b6b;
  }
  * { margin: 0; padding: 0; box-sizing: border-box; }
  html, body { width: 1200px; height: 1000px; overflow: hidden; }
  body {
    background: var(--backdrop);
    font-family: "Poppins", sans-serif;
    position: relative;
  }
  .card {
    position: absolute;
    top: 193px;
    width: 351px;
    height: 615px;
    border-radius: 28px;
  }
  .card--back {
    left: 247px;
    background: var(--card-dark);
    display: flex;
    align-items: center;
    justify-content: center;
  }
  .card--front {
    left: 657px;
    background: var(--card-light);
    text-align: center;
  }
  .wordmark {
    font-family: "Poppins", sans-serif;
    font-weight: 800;
    letter-spacing: 3px;
    line-height: 1;
  }
  .card--back .wordmark {
    color: var(--card-dark-mark);
    font-size: 44px;
    margin-top: -8px;
  }
  .holder { position: absolute; top: 184px; left: 0; right: 0; }
  .holder__name {
    font-weight: 600;
    font-size: 23px;
    color: var(--brand-navy);
    line-height: 30px;
  }
  .holder__role {
    font-weight: 400;
    font-size: 13px;
    letter-spacing: 1.6px;
    color: var(--brand-sky);
    line-height: 18px;
  }
  .contact-icons {
    position: absolute;
    top: 259px; left: 0; right: 0;
    display: flex;
    justify-content: center;
    gap: 7px;
  }
  .contact-icons svg { width: 38px; height: 38px; display: block; }
  .contact-details {
    position: absolute;
    top: 323px; left: 0; right: 0;
    font-weight: 300;
    font-size: 18px;
    line-height: 24px;
    color: var(--body-grey);
  }
  .contact-details .address { margin-top: 24px; }
  .card--front .wordmark {
    position: absolute;
    left: 0; right: 0;
    top: 532px;
    font-size: 30px;
    color: var(--brand-navy);
  }
</style>
</head>
<body>
  <section class="card card--back">
    <div class="wordmark">TOVRIN</div>
  </section>

  <section class="card card--front">
    <div class="holder">
      <div class="holder__name">Warren Halbeck</div>
      <div class="holder__role">GENERAL MANAGER</div>
    </div>

    <div class="contact-icons">
      <svg viewBox="0 0 38 38" aria-label="Phone">
        <circle cx="19" cy="19" r="19" fill="var(--brand-sky)"/>
        <path d="M13.5 11.5c1-.8 2-.6 2.6.4l1.5 2.6c.5.9.3 1.7-.5 2.3l-.9.7c.8 1.9 2.3 3.5 4.2 4.5l.8-.9c.6-.8 1.5-.9 2.3-.4l2.6 1.6c1 .6 1.1 1.7.3 2.6l-1 1c-1.3 1.3-3.4 1.2-5.6-.1-3.2-1.9-5.8-4.7-7.2-7.9-.9-2.2-.7-4.1.6-5.3z" fill="#fff"/>
      </svg>
      <svg viewBox="0 0 38 38" aria-label="Email">
        <circle cx="19" cy="19" r="19" fill="var(--brand-sky)"/>
        <rect x="11" y="13" width="16" height="12" rx="1" fill="#fff"/>
        <path d="M11.5 13.5 19 20l7.5-6.5" fill="none" stroke="var(--brand-sky)" stroke-width="1.4"/>
      </svg>
      <svg viewBox="0 0 38 38" aria-label="Website">
        <circle cx="19" cy="19" r="19" fill="var(--brand-sky)"/>
        <g fill="none" stroke="#fff" stroke-width="1.5">
          <circle cx="19" cy="19" r="8"/>
          <ellipse cx="19" cy="19" rx="3.5" ry="8"/>
          <path d="M11 19h16M12.3 15h13.4M12.3 23h13.4"/>
        </g>
      </svg>
      <svg viewBox="0 0 38 38" aria-label="Address">
        <circle cx="19" cy="19" r="19" fill="var(--brand-sky)"/>
        <path d="M19 9.5c-3.8 0-6.5 2.8-6.5 6.4 0 4.5 6.5 12.6 6.5 12.6s6.5-8.1 6.5-12.6c0-3.6-2.7-6.4-6.5-6.4z" fill="#fff"/>
        <circle cx="19" cy="16" r="2.4" fill="var(--brand-sky)"/>
      </svg>
    </div>

    <div class="contact-details">
      <div class="phone">0472 915 348</div>
      <div class="email">Warren.halbeck@tovrin.com.au</div>
      <div class="web">www.tovrin.com.au</div>
      <div class="address">87 Marrow Ave,<br>Pendlebay, QLD, 4023</div>
    </div>

    <div class="wordmark">TOVRIN</div>
  </section>
</body>
</html>
```